Food and Beverage Business Cards

We need business cards with logo designs for a consultant in the food and beverage industry. We specialize in helping restaurants fix operational and management problems.
Specific areas of expertise include:
-Steps of service
-Staff management tools
-Standard operating procedures
-Profit and loss management
-Inventory
-Point of sales
-Bar Menu
-Mystery shopper service
-Handling and managing suppliers

Target Market(s)

Restaurant and bar owners and managers

Industry/Entity Type

Business

Contact Information for Business Card

Mathieu Girardot
Q&T Consulting
phone: 15027390614
mathqt@sampleinbox.com

Font styles to use
Other font styles liked:
• Check out the screen shot font idea

Colors

Designer to choose colors to be used in the design.

Requirements
Must have
• Must include QR code (See attachment)
• Logo should reflect our specific focus on the drinks side of the industry.
• Areas of Expertise:
• -Service Steps
• -Staff management tools
• -S.O.P
• -P&L Management
• -Inventory
• -P.O.S
• -Bar Menu
• -Mystery Shopper Service
• -Handling and Managing Suppliers

```html
<!DOCTYPE html>
<html lang="en">
<head>
<meta charset="UTF-8">
<title>Q&amp;T Consulting – Business Cards</title>
<link rel="stylesheet" href="https://fonts.googleapis.com/css2?family=Open+Sans:wght@400;700&display=swap">
<style>
  :root {
    --backdrop: #3a302b;
    --card: #151515;
    --card-edge: #222222;
    --ink-white: #f4f4f4;
    --ink-grey: #b9b9b9;
    --ink-mark: #a9a9a9;
    --badge-green: #2f4a2c;
    --badge-grey: #8a8a8a;
    --badge-light: #cfcfcf;
  }
  * { margin: 0; padding: 0; box-sizing: border-box; }
  html, body {
    width: 1200px;
    height: 864px;
    overflow: hidden;
    background: var(--backdrop);
    font-family: "Open Sans", Arial, sans-serif;
  }
  .canvas {
    position: relative;
    width: 1200px;
    height: 864px;
  }
  .card {
    position: absolute;
    width: 540px;
    height: 310px;
    background: var(--card);
    border: 1px solid var(--card-edge);
    box-shadow: 0 14px 30px rgba(0,0,0,0.45);
  }
  .card--expertise { left: 50px; top: 110px; }
  .card--contact { left: 610px; top: 440px; }

  /* Expertise side */
  .expertise-mark {
    position: absolute;
    left: 0; right: 0; top: 36px;
    text-align: center;
    font-size: 82px;
    font-weight: 700;
    color: var(--ink-mark);
    letter-spacing: 2px;
    line-height: 1;
  }
  .badges {
    position: absolute;
    right: 26px; top: 26px;
    display: flex;
    gap: 8px;
  }
  .badge {
    width: 42px; height: 42px;
    border-radius: 50%;
  }
  .badge--green { background: var(--badge-green); }
  .badge--grey { background: var(--badge-grey); }
  .badge--light { background: var(--badge-light); }
  .expertise-title {
    position: absolute;
    left: 0; right: 0; top: 150px;
    text-align: center;
    font-size: 19px;
    font-weight: 700;
    color: var(--ink-grey);
  }
  .expertise-list {
    position: absolute;
    left: 20px; right: 20px; top: 184px;
    text-align: center;
    font-size: 14px;
    line-height: 1.45;
    color: var(--ink-grey);
  }

  /* Contact side */
  .contact-mark {
    position: absolute;
    left: 0; right: 0; top: 60px;
    text-align: center;
    color: var(--ink-white);
    font-weight: 700;
    line-height: 1;
  }
  .contact-mark__name { font-size: 78px; letter-spacing: 2px; }
  .contact-mark__place { font-size: 20px; letter-spacing: 5px; margin-top: 4px; }
  .person {
    position: absolute;
    right: 300px; top: 208px;
    text-align: right;
    color: var(--ink-white);
  }
  .person__name { font-size: 17px; font-weight: 700; }
  .person__role { font-size: 14px; }
  .divider {
    position: absolute;
    left: 258px; top: 206px;
    width: 1px; height: 58px;
    background: var(--ink-white);
  }
  .contact-lines {
    position: absolute;
    left: 278px; top: 216px;
    color: var(--ink-white);
    font-size: 15px;
    line-height: 1.6;
  }
  .contact-line { display: flex; align-items: center; gap: 8px; }
  .contact-line svg { width: 13px; height: 13px; fill: var(--ink-white); }
</style>
</head>
<body>
<main class="canvas">
  <section class="card card--expertise">
    <div class="expertise-mark">Q&amp;T</div>
    <div class="badges">
      <span class="badge badge--green"></span>
      <span class="badge badge--grey"></span>
      <span class="badge badge--light"></span>
    </div>
    <h2 class="expertise-title">Areas of Expertise</h2>
    <p class="expertise-list">
      Service Steps | Staff management tools | S.O.P | P&amp;L Management<br>
      Inventory | P.O.S | Bar Menu | Mystery Shopper Service<br>
      Handling and Managing Suppliers
    </p>
  </section>

  <section class="card card--contact">
    <div class="contact-mark">
      <div class="contact-mark__name">Q&amp;T</div>
      <div class="contact-mark__place">dalton</div>
    </div>
    <div class="person">
      <div class="person__name">Mathieu Girardot</div>
      <div class="person__role">Q&amp;T Consulting</div>
    </div>
    <span class="divider"></span>
    <div class="contact-lines">
      <div class="contact-line">
        <svg viewBox="0 0 16 16" aria-hidden="true"><path d="M2 6c0-3 3-4 6-4s6 1 6 4v1h-3V5H5v2H2zM4 8h8l2 6H2z"/></svg>
        <span>15027390614</span>
      </div>
      <div class="contact-line">
        <svg viewBox="0 0 16 16" aria-hidden="true"><path d="M1 3h14v10H1z M1 3l7 6 7-6" stroke="#151515" stroke-width="1"/></svg>
        <span>mathqt@sampleinbox.com</span>
      </div>
    </div>
  </section>
</main>
</body>
</html>
```